R. Talmont Realty, Inc business card (2 sided), letterhead (1 sided) & #10 envelope (1 sided)

business card of standard size utilizing the attached logo. Side one with logo, Owen Talmont (my name), President / Broker (title), 805-317-2684 (phone), www.rtalmontrealty.example (website), 1726 Harlow Avenue, Suite 4052 San Luis Obiso, CA 93628 (business address) owen.rtalmontrealty@mailbox.example (e-mail address),
Side two - Log

Letterhead and #10 envelope in the same theme
Updates

Project Deadline Extended
Reason: I think a 2 day deadline may be a bit ambitious on my part. I have extended the deadline to 4 days. Thanks!

Industry/Entity Type

Business

```html
<!DOCTYPE html>
<html lang="en">
<head>
<meta charset="utf-8">
<title>R. Talmont Realty, Inc — Business Card</title>
<link rel="stylesheet" href="https://fonts.googleapis.com/css2?family=Noto+Serif:wght@700&family=Open+Sans:wght@400&display=swap">
<style>
  :root {
    --backdrop: #e9e6e1;
    --card: #ffffff;
    --card-edge: #3a3a3a;
    --brand-blue: #1f6e92;
    --ink: #2b2b2b;
    --rule: #c9c9c9;
  }
  * { margin: 0; padding: 0; box-sizing: border-box; }
  html, body {
    width: 1200px; height: 1183px; overflow: hidden;
    background: var(--backdrop);
  }
  .card {
    position: absolute;
    width: 912px; height: 519px;
    background: var(--card);
    border: 1.5px solid var(--card-edge);
  }
  .card--front { left: 237px; top: 52px; }
  .card--back  { left: 31px;  top: 616px; }

  .brand {
    position: absolute; left: 0; right: 0;
    display: flex; align-items: center; justify-content: center; gap: 16px;
    font-family: "Noto Serif", Georgia, serif;
    font-weight: 700; font-size: 44px; color: var(--brand-blue);
    white-space: nowrap;
  }
  .brand__mark { width: 22px; height: 22px; background: var(--brand-blue); }
  .card--front .brand { top: 130px; }
  .card--back .brand  { top: 210px; }

  .person {
    position: absolute; right: 522px; top: 362px; text-align: right;
    font-family: "Noto Serif", Georgia, serif; white-space: nowrap;
  }
  .person__name { font-size: 29px; font-weight: 700; color: var(--brand-blue); line-height: 1.25; }
  .person__title { font-size: 24px; font-weight: 700; color: var(--ink); line-height: 1.5; }

  .divider {
    position: absolute; left: 425px; top: 344px;
    width: 1.5px; height: 117px; background: var(--rule);
  }
  .contact {
    position: absolute; left: 440px; top: 348px; list-style: none;
    font-family: "Open Sans", Arial, sans-serif; font-size: 20px; color: var(--ink);
  }
  .contact li { display: flex; align-items: center; gap: 8px; height: 42px; white-space: nowrap; }
  .contact svg { width: 18px; height: 18px; flex: none; }

  .web {
    position: absolute; left: 0; right: 0; top: 430px; text-align: center;
    font-family: "Open Sans", Arial, sans-serif; font-size: 28px;
    letter-spacing: 3.5px; color: var(--ink);
  }
</style>
</head>
<body>
  <section class="card card--front" aria-label="Business card, front">
    <div class="brand"><span class="brand__mark"></span>R. Talmont Realty, Inc</div>

    <div class="person">
      <p class="person__name">Owen Talmont</p>
      <p class="person__title">President / Broker</p>
    </div>
    <div class="divider"></div>
    <ul class="contact">
      <li>
        <svg viewBox="0 0 18 18" aria-hidden="true"><circle cx="9" cy="9" r="8" fill="none" stroke="#1f6e92" stroke-width="1.5"/><path d="M6 5.5c-.6 2.8 1.6 6.4 5 7l1.2-1.6-1.8-1-1 .8c-1-.5-1.9-1.5-2.2-2.6l.9-.9-.8-1.9z" fill="#1f6e92"/></svg>
        805-317-2684
      </li>
      <li>
        <svg viewBox="0 0 18 18" aria-hidden="true"><circle cx="9" cy="9" r="9" fill="#1f6e92"/><rect x="4" y="6" width="10" height="7" fill="#fff"/><path d="M4 6l5 4 5-4" fill="none" stroke="#1f6e92" stroke-width="1.2"/></svg>
        owen.rtalmontrealty@mailbox.example
      </li>
      <li>
        <svg viewBox="0 0 18 18" aria-hidden="true"><circle cx="9" cy="9" r="8" fill="none" stroke="#1f6e92" stroke-width="1.5"/><ellipse cx="9" cy="9" rx="3.5" ry="8" fill="none" stroke="#1f6e92" stroke-width="1.2"/><path d="M1 9h16M2.5 5h13M2.5 13h13" stroke="#1f6e92" stroke-width="1.2"/></svg>
        www.rtalmontrealty.example
      </li>
    </ul>
  </section>

  <section class="card card--back" aria-label="Business card, back">
    <div class="brand"><span class="brand__mark"></span>R. Talmont Realty, Inc</div>
    <p class="web">www.rtalmontrealty.example</p>
  </section>
</body>
</html>
```